Business Card for Beach theme sports bar called MORVIN

I need a business card designed for our employees, front and back. This will be used by the employees of two business locations to hand out to customers. I've attached the previous business cards we used at one time for a Dantells (it is now Morvin). Looking for a fresh new card that is elegant but has character.

Target Market(s)

30-60, middle class

Contact Information for Business Card

We are a beach bar and sports bar. I am looking for an elegant business card with the front to have the MORVIN logo. Then on the back I need it to allow a space for employees to write their names and for them to write in their schedule. I have attached our old cards with our old name Dantells so you can pull everything we need on the cards. one thing is missing is we have another location at 2615 W Calder Ridge Rd with a number of 702-418-9053. Since we will use it for both locations it should allow the employee to circle or check mark the bar which they work at.

Font styles to use
Sans Serif

Requirements
Must have
• We are looking for some fresh ideas for the business card. Something that will really stick out to customers when the staff hands them out. Creativity will be looked at positively, but we still want it to look upscale and fun.

```html
<!DOCTYPE html>
<html lang="en">
<head>
<meta charset="utf-8">
<title>Morvin Business Card</title>
<link rel="stylesheet" href="https://fonts.googleapis.com/css2?family=Work+Sans:wght@400;500&display=swap">
<style>
  :root {
    --stage: #1c1c1c;
    --card: #262626;
    --card-edge: #2e2e2e;
    --ink: #f2f2f2;
    --ink-soft: #d6d6d6;
    --rule: #8a8a8a;
    --foil: #a9a9a9;
  }
  * { box-sizing: border-box; margin: 0; padding: 0; }
  html, body { width: 1200px; height: 900px; overflow: hidden; }
  body {
    background: var(--stage);
    font-family: "Work Sans", sans-serif;
    display: flex;
    flex-direction: column;
    align-items: center;
    justify-content: center;
    gap: 40px;
  }
  .card {
    width: 660px;
    height: 377px;
    background: linear-gradient(135deg, var(--card-edge), var(--card));
    box-shadow: 0 14px 30px rgba(0,0,0,0.55);
    position: relative;
  }
  .card-front {
    display: flex;
    align-items: center;
    justify-content: center;
  }
  .brand-foil {
    font-size: 64px;
    font-weight: 500;
    color: var(--foil);
    letter-spacing: 1px;
  }
  .card-back {
    display: flex;
    align-items: center;
  }
  .brand-block {
    width: 290px;
    display: flex;
    justify-content: center;
  }
  .brand-name {
    font-size: 60px;
    font-weight: 500;
    color: var(--ink);
    letter-spacing: 1px;
  }
  .divider {
    width: 2px;
    height: 270px;
    background: var(--ink);
  }
  .contact {
    padding-left: 40px;
    width: 326px;
    color: var(--ink);
  }
  .write-in {
    display: flex;
    align-items: flex-end;
    gap: 10px;
    height: 28px;
  }
  .write-in-label {
    font-size: 12px;
    font-weight: 500;
    letter-spacing: 1.5px;
    line-height: 1;
  }
  .write-in-line {
    flex: 1;
    border-bottom: 1px solid var(--rule);
  }
  .write-in-extra { height: 26px; border-bottom: 1px solid var(--rule); }
  .locations {
    margin-top: 16px;
    display: flex;
    flex-direction: column;
    gap: 8px;
  }
  .location {
    display: flex;
    gap: 10px;
    align-items: flex-start;
  }
  .check-box {
    width: 13px;
    height: 13px;
    border: 1.3px solid var(--ink);
    margin-top: 3px;
    flex: none;
  }
  .location-text {
    font-size: 14px;
    line-height: 1.4;
    letter-spacing: 0.4px;
  }
  .location-phone { color: var(--ink-soft); }
  .contact-lines { margin-top: 10px; }
  .contact-line {
    display: flex;
    align-items: center;
    gap: 10px;
    font-size: 15px;
    line-height: 1.6;
    letter-spacing: 0.5px;
  }
  .contact-line svg { width: 12px; height: 12px; flex: none; }
</style>
</head>
<body>
  <section class="card card-front">
    <span class="brand-foil">Morvin</span>
  </section>

  <section class="card card-back">
    <div class="brand-block">
      <span class="brand-name">Morvin</span>
    </div>
    <div class="divider"></div>
    <div class="contact">
      <div class="write-in">
        <span class="write-in-label">NAME</span>
        <span class="write-in-line"></span>
      </div>
      <div class="write-in">
        <span class="write-in-label">SCHEDULE</span>
        <span class="write-in-line"></span>
      </div>
      <div class="write-in-extra"></div>

      <div class="locations">
        <div class="location">
          <span class="check-box"></span>
          <p class="location-text">58 Harbor Lane, Brookhaven, NZ, 8042<br><span class="location-phone">(514) 555-0172</span></p>
        </div>
        <div class="location">
          <span class="check-box"></span>
          <p class="location-text">2615 W Calder Ridge Rd<br><span class="location-phone">702-418-9053</span></p>
        </div>
      </div>

      <div class="contact-lines">
        <p class="contact-line">
          <svg viewBox="0 0 12 12" aria-hidden="true"><rect x="1" y="2.5" width="10" height="7" fill="none" stroke="#f2f2f2" stroke-width="1.2"/><path d="M1 2.5 L6 6.5 L11 2.5" fill="none" stroke="#f2f2f2" stroke-width="1.2"/></svg>
          info@morvin.com
        </p>
        <p class="contact-line">
          <svg viewBox="0 0 12 12" aria-hidden="true"><circle cx="6" cy="6" r="5" fill="none" stroke="#f2f2f2" stroke-width="1.1"/><ellipse cx="6" cy="6" rx="2.2" ry="5" fill="none" stroke="#f2f2f2" stroke-width="1"/><path d="M1 6 H11" stroke="#f2f2f2" stroke-width="1"/></svg>
          www.morvin.com
        </p>
      </div>
    </div>
  </section>
</body>
</html>
```